Job application set/company logo

My resume, profile and project file need to be designed in a common, fresh business design, not too playful and colourful
Potentially a logo for my company called Silver Reed Consulting needs to be designed in a second step. My company is consulting in digitalization and business transformation.

```html
<!DOCTYPE html>
<html lang="en">
<head>
<meta charset="utf-8">
<title>Martin Kessler – Resume</title>
<link rel="stylesheet" href="https://fonts.googleapis.com/css2?family=Poppins:wght@500;600;700&family=Open+Sans:wght@400;600&display=swap">
<style>
  :root{
    --bg:#e8e8e9;
    --paper:#ffffff;
    --navy:#1b3f73;
    --blue:#1c80cf;
    --blue-dark:#0f5ea3;
    --ink:#16305d;
    --text:#3b4150;
    --white:#ffffff;
  }
  *{box-sizing:border-box;margin:0;padding:0}
  html,body{width:739px;height:1200px;overflow:hidden;background:var(--bg)}
  body{position:relative;font-family:"Open Sans",Arial,sans-serif;color:var(--text)}
  .sheet{position:absolute;left:162px;width:615px;height:870px;background:var(--paper);
    transform:scale(.675);transform-origin:top left;box-shadow:0 6px 20px rgba(0,0,0,.18)}
  .sheet--one{top:6px}
  .sheet--two{top:607px}
  .sidebar{position:absolute;left:37px;top:31px;width:231px;height:805px;background:var(--navy);color:var(--white);padding:0 12px}
  .photo{margin-top:9px;width:207px;height:185px;border:3px solid #fff;border-radius:0 0 22px 0;
    background:linear-gradient(160deg,#c9c3bb 0%,#8d8a88 45%,#2a2c33 100%)}
  .name{font-family:"Poppins",sans-serif;font-weight:600;font-size:18.5px;margin:20px 0 14px;letter-spacing:.2px}
  .side-band{position:relative;margin:0 -2px 8px 0;background:var(--blue);font-family:"Poppins",sans-serif;font-weight:600;
    font-size:13.5px;text-align:center;height:20px;line-height:20px;letter-spacing:.4px}
  .contact{list-style:none;font-family:"Poppins",sans-serif;font-weight:600;font-size:9.5px;line-height:13px}
  .contact li{display:flex;gap:8px;margin-bottom:3px}
  .contact svg{flex:none;width:10px;height:10px;margin-top:1px}
  .contact .web{font-size:7.6px}
  .side-head{font-family:"Poppins",sans-serif;font-weight:500;font-size:11px;margin:10px 0 10px;letter-spacing:.3px}
  .side-item{font-size:9.3px;line-height:11.5px;margin-bottom:14px}
  .side-item b{font-family:"Poppins",sans-serif;font-weight:600}
  .main{position:absolute;left:289px;top:42px;width:302px}
  .band{position:relative;background:var(--blue);color:#fff;font-family:"Poppins",sans-serif;font-weight:600;font-size:15.5px;
    height:24px;line-height:24px;padding-left:12px;letter-spacing:.4px}
  .band::after{content:"";position:absolute;right:0;top:-7px;border-left:9px solid transparent;border-bottom:7px solid var(--blue-dark)}
  .timeline{position:relative;padding-left:14px;margin-top:12px}
  .timeline::before{content:"";position:absolute;left:4px;top:4px;bottom:0;width:1px;background:#555}
  .topic{position:relative;font-family:"Poppins",sans-serif;font-weight:600;color:var(--ink);font-size:12px;line-height:14px;margin-bottom:5px}
  .topic::before{content:"";position:absolute;left:-12px;top:4px;width:5px;height:5px;border-radius:50%;background:var(--ink)}
  .list{list-style:none;margin-bottom:7px}
  .list li{position:relative;padding-left:18px;font-size:6.7px;line-height:8px;margin-bottom:7px;color:#333}
  .list li::before{content:"";position:absolute;left:2px;top:1px;width:5px;height:5px;border-radius:50%;border:1.5px solid var(--blue)}
  .list--dot li::before{border:none;background:#444;width:2.5px;height:2.5px;left:4px;top:2.5px}
  .role{font-family:"Poppins",sans-serif;font-weight:600;color:var(--ink);font-size:12.5px;margin:10px 0 6px;position:relative}
  .role::before{content:"";position:absolute;left:-12px;top:6px;width:5px;height:5px;border-radius:50%;background:var(--ink)}
  .entry{display:flex;align-items:baseline;gap:10px;font-family:"Poppins",sans-serif;font-weight:600;color:#111;font-size:11px;margin:2px 0 6px}
  .entry::before{content:"";width:5px;height:5px;border-radius:50%;border:1.5px solid var(--blue);flex:none;margin-right:-6px}
  .entry .date{font-size:6.8px;color:var(--blue-dark);white-space:nowrap}
  .entry .date.right{margin-left:auto}
  .entry--stack{line-height:13px}
  .date-line{text-align:right;font-family:"Poppins",sans-serif;font-weight:600;font-size:6.8px;color:var(--blue-dark);margin:-2px 0 2px}
  .side-block{font-size:9.8px;line-height:11.8px;padding:0 4px;margin-bottom:14px}
  .side-block--pairs div{display:flex;margin-bottom:10px}
  .side-block--pairs span:first-child{width:68px}
  .sidebar--right{padding-top:15px}
  .main--two{left:286px;top:31px;width:300px}
  .company{font-family:"Poppins",sans-serif;font-weight:600;color:var(--ink);font-size:12px;margin-bottom:6px;position:relative}
  .company::before{content:"";position:absolute;left:-12px;top:5px;width:5px;height:5px;border-radius:50%;background:var(--ink)}
</style>
</head>
<body>

<section class="sheet sheet--one">
  <aside class="sidebar">
    <div class="photo" role="img" aria-label="Portrait photo of the applicant in a dark suit"></div>
    <h1 class="name">MARTIN KESSLER</h1>
    <div class="side-band">PERSONALINFOS</div>
    <ul class="contact">
      <li><svg viewBox="0 0 10 10"><rect x=".5" y="2" width="9" height="6.5" fill="none" stroke="#fff"/><path d="M.5 2 5 6 9.5 2" fill="none" stroke="#fff"/></svg>martin.kessler@mailbox.example</li>
      <li><svg viewBox="0 0 10 10"><path d="M5 9.5C2 6 2 5 2 4a3 3 0 0 1 6 0c0 1 0 2-3 5.5z" fill="none" stroke="#fff"/><circle cx="5" cy="4" r="1" fill="#fff"/></svg>Lindenweg 12 – 53111<br>Bonn , Germany</li>
      <li><svg viewBox="0 0 10 10"><rect x=".5" y="1.5" width="9" height="8" fill="none" stroke="#fff"/><path d="M.5 4h9M3 .5v2M7 .5v2" stroke="#fff"/></svg>17 . 03 . 1969</li>
      <li class="web"><svg viewBox="0 0 10 10"><rect x="1" y="1" width="8" height="8" fill="#fff"/></svg>profiles.example / martinkessler</li>
    </ul>
    <div class="side-band" style="margin-top:8px">QUALIFICATIONS</div>
    <h2 class="side-head">CORE COMPETENCIES</h2>
    <p class="side-item"><b>Passionate Digital Transformation Leader</b> with track record of launching and growing business</p>
    <p class="side-item"><b>Entrepreneurial background</b> with network to global innovation hubs</p>
    <p class="side-item"><b>Strong Product &amp; Innovation competence</b> with a clear understanding of market needs</p>
    <p class="side-item"><b>Track record in driving partnerships</b> into highly</p>
    <h2 class="side-head">ACCOMPLISHMENTS</h2>
    <p class="side-item">Mentor at Chipwell’s Launchpad program for startups</p>
    <p class="side-item">Crash Course in Data Science at Eastbrook University</p>
    <p class="side-item">Intro to Blockchain Technology at Westmoor Institute</p>
    <p class="side-item">Level 1, Certified Agile Team Lead, Agile Guild</p>
    <p class="side-item">Leadership Excellence Program at Harbor Business School</p>
  </aside>

  <main class="main">
    <h2 class="band">PROFILE &amp; ACHIEVEMENTS</h2>
    <div class="timeline">
      <h3 class="topic">GUIDING ENTREPRENEURIAL INNOVATIONS</h3>
      <ul class="list">
        <li>Define a way forward for Veltrix’s Messaging business</li>
        <li>Shape a venture for Norvane in the eMobility segment</li>
        <li>Build a joint venture of Nordtel Group and Lumora Optics for the development of connected smart glasses</li>
      </ul>
      <h3 class="topic">LEADING GLOBAL PARTNER SHIP NETWORKS</h3>
      <ul class="list">
        <li>Overcome strategic objectives and form an alliance of Searchly and Veltrix in Messaging</li>
        <li>Position Nordtel Group as first choice for Orchard Devices smartphones with a purchase volume of more than 2 billion euro</li>
        <li>Create exclusive advantages for Nordtel Group customers through partnerships with major innovators like Orchard Devices and Riverstone Retail</li>
      </ul>
      <h3 class="topic">DELIVERY-ORIENTED PRODUCT LEADER</h3>
      <ul class="list">
        <li>Manage the roll out of new GSM-R Units to &gt;5000 vehicles for National Rail Co in logistics and technical integration</li>
        <li>Open the door for IoT business of Quentis to access European telcos</li>
        <li>Develop a consistent Horizon@home experience and build the corresponding device portfolio supporting DSL, TV, Smart Home</li>
      </ul>
    </div>

    <h2 class="band" style="font-size:17px;margin-top:2px">EXPERIENCE ( exemplary )</h2>
    <div class="timeline" style="margin-top:4px">
      <h3 class="role">SENIOR ADVISOR ( self -employed )</h3>
      <p class="entry">Incubra Corporate Startups <span class="date">10/2020 – Present</span></p>
      <ul class="list list--dot"><li>Venture building (e.g. with Norvane and NG)</li><li>Derive a product strategy and go to market plan</li></ul>
      <p class="entry">Key Success:</p>
      <ul class="list list--dot"><li>Successful start of Orbiton, the Norvane eMobility venture</li></ul>
      <p class="entry">Quentis Communications <span class="date">08/2021 – Present</span></p>
      <ul class="list list--dot"><li>Define a strategy how to approach telco carriers</li><li>Evaluate business models to engage with distributors</li></ul>
      <p class="entry">Key Success:</p>
      <ul class="list list--dot"><li>Growth through new distribution channels via carriers</li></ul>
      <p class="entry">Veltrix <span class="date right" style="margin-right:14px">04/2021 – 04/2022</span></p>
      <ul class="list list--dot"><li>Evaluation of the global messaging business</li><li>Define a new strategy for messaging in Veltrix</li><li>Implement a new independent business unit for SaaS</li></ul>
      <p class="entry">Key Success:</p>
      <ul class="list list--dot"><li>Successful start of the new business unit</li></ul>
      <p class="entry">Quadrant One Consulting <span class="date right" style="margin-right:14px">10/2020 – 12/2022</span></p>
      <ul class="list list--dot"><li>Steering of a group wide exchange of GSM-R equipment</li></ul>
      <p class="entry">Key Success:</p>
      <ul class="list list--dot"><li>Improvement of the mobile connectivity experience for customers of the National Rail Co</li></ul>
    </div>
  </main>
</section>

<section class="sheet sheet--two">
  <aside class="sidebar sidebar--right">
    <div class="side-band" style="margin-bottom:18px">UNIVERSITY</div>
    <p class="side-block">Executive Leadership Development Program at Pinecrest Graduate School of Business (2016)</p>
    <p class="side-block">Diploma in Electrical Engineering at Rheinfeld Technical University (1987–1994)</p>
    <div class="side-band" style="margin-bottom:14px">LANGUAGES</div>
    <div class="side-block side-block--pairs">
      <div><span>German</span><span>Native</span></div>
      <div><span>English</span><span>Full professional<br>proficiency</span></div>
    </div>
    <div class="side-band" style="margin-bottom:14px">ACTIVITIES</div>
    <div class="side-block">
      <p style="margin-bottom:13px">Sport: Skiing, Tennis, Hiking, Yoga</p>
      <p style="margin-bottom:13px">Music: Classical Piano</p>
      <p>Travelling: Europe, Africa, America</p>
    </div>
    <div class="side-band" style="margin-bottom:20px">REFERENCES</div>
    <p class="side-block">Lukas Brenner, CEO Nordtel Group</p>
    <p class="side-block">Anna Varga, SVP Global Strategic Projects and Marketing Partnerships, Nordtel Group</p>
    <p class="side-block">Paul Renard, formerly CEO Taro Mobile Corporation</p>
  </aside>

  <main class="main main--two">
    <div class="timeline" style="margin-top:0">
      <h3 class="company">NORDTEL GROUP , BONN</h3>
      <p class="entry entry--stack">Senior Vice President<br>Connected Devices <span class="date right">08/2011 – 07/2020</span></p>
      <ul class="list list--dot">
        <li>Management of the global partnerships with Orchard Devices, Kumo Electronics</li>
        <li>Board member of Visora Inc., a JV of NG and Lumora Optics</li>
        <li>Driving the entire portfolio of devices for the NG group including</li>
      </ul>
      <p class="entry">Key Success:</p>
      <ul class="list list--dot">
        <li>Managing a turnover of more than 3 billion euros with devices across the Nordtel group</li>
        <li>Development of the first Horizon Voice Speaker</li>
        <li>Foundation of the Visora joint venture</li>
      </ul>
      <p class="entry entry--stack">Vice President Product<br>Management Mobile <span class="date right">04/2008 – 07/2011</span></p>
      <ul class="list list--dot">
        <li>Introduction of the international portfolio of mobile phones in Nordtel Group</li>
        <li>Project lead for key initiatives, e.g. introduction of OpalOS Wearables, Voice Controlled Devices and Virtual Reality Glasses</li>
      </ul>
      <p class="entry">Key Success:</p>
      <ul class="list list--dot">
        <li>Successful introduction of the first OpalOS phone in an exclusive partnership with Searchly and Taro Mobile</li>
        <li>Development of the NG App portfolio for PearOS and OpalOS</li>
      </ul>
      <h3 class="company" style="margin-top:12px">TELVIA INTERNATIONAL , BONN</h3>
      <p class="date-line">09/1994 – 03/2008</p>
      <p class="entry">Head of Client Integration/ISP Products</p>
      <ul class="list list--dot">
        <li>Conception and development of a branded mobile phone</li>
        <li>Transformation of product management from voice-centric into mobile internet business</li>
      </ul>
      <p class="entry entry--stack">Project Lead Personal<br>Communication Services</p>
      <ul class="list list--dot">
        <li>Project lead of the first FMC product combining fixed and mobile communication on one bill with one device and one service</li>
      </ul>
      <p class="entry">Project Engineering</p>
      <ul class="list list--dot">
        <li>Project lead “Short Message Service Center”</li>
        <li>Voice quality assurance: Design of a new measurement system and implementation in C++</li>
        <li>Audits of system technology suppliers</li>
      </ul>
    </div>
  </main>
</section>

</body>
</html>
```